Jolly Hounds Dog Behaviour, Training and Natural Healthcare Business Card Design

I am an experienced and qualified dog behavioural trainer and natural animal healthcare consultant offering a range of services to help pet dog owners with the "whole dog".
COLOURS: A soft light blue in the background - can be fading out or split, red should also feature
LOGO: Dog, healing hands, silhouette, shadow
SERVICES: Behaviour Consults, Training, Complex Skills Coaching Walking Coaching, Diet & Nutrition, Environmental Enrichment, Lifestyle and Lifestage Adaptations, Massage, Natural Health Options
BY LINE: Happy Dogs, Happy Owners
VALUES: Promoting communication and connection between dogs and their owners.
FOCUS: Nutritional guidance and environmental adaptation are often needed to complete the package and increase the success rate of training and behaviour modification.

Target Market(s)

Everyone who has a dog who they wish to improve their relationship with

Industry/Entity Type

Communication

Contact Information for Business Card

Jolly Hounds, Rebecca Thornbury, 0427 861350, jollyhounds7@fernpost.example, www.jollyhounds7.example, Qualified Dog Behavioural Trainer and Natural Animal Healthcare Consultant

Font styles to use
Sans Serif
Script

Colors
85cae6
ec2027

Requirements
Must have
• A clear indication that it is a dog services business. A raised feature
Should not have
• Pawprints, cartoons

```html
<!DOCTYPE html>
<html lang="en">
<head>
<meta charset="utf-8">
<title>Jolly Hounds – Business Card</title>
<link rel="stylesheet" href="https://fonts.googleapis.com/css2?family=Archivo:wght@800&family=Carlito:wght@400;700&family=PT+Sans+Narrow&family=Dancing+Script:wght@600&display=swap">
<style>
  :root {
    --page-bg: #e8f4fa;
    --brand-blue: #85cae6;
    --brand-blue-soft: #d4edf7;
    --brand-red: #ec2027;
    --card-white: #ffffff;
    --band-black: #0b0b0b;
    --ink: #111111;
    --icon-fill: #e4e4e4;
    --icon-ring: #9a9a9a;
    --icon-ink: #1a1a1a;
    --contact-text: #ffffff;
    --photo-tan: #c7904f;
    --photo-dark: #2a2118;
  }
  * { margin: 0; padding: 0; box-sizing: border-box; }
  html, body { width: 1200px; height: 900px; overflow: hidden; }
  body { background: var(--page-bg); position: relative; }

  .business-card {
    position: absolute;
    left: 100px; top: 164px;
    width: 1000px; height: 572px;
    background: linear-gradient(180deg, var(--brand-blue-soft) 0%, var(--card-white) 70%);
    overflow: hidden;
    box-shadow: 0 6px 24px rgba(0,0,0,.2);
  }

  .contact-band {
    position: absolute; left: 0; right: 0; bottom: 0; top: 332px;
    background: var(--band-black);
    border-top: 5px solid var(--brand-red);
  }

  .panel-divider {
    position: absolute; left: 580px; top: 0; height: 332px;
    border-left: 3px solid var(--brand-red);
  }

  .photo-panel {
    position: absolute; left: 583px; top: 0; width: 417px; height: 440px;
    background: linear-gradient(180deg, var(--brand-blue-soft) 0%, var(--card-white) 60%);
  }
  .dog-photo {
    position: absolute; left: 50px; top: 90px; width: 340px; height: 350px;
    background: radial-gradient(ellipse at 62% 40%, var(--photo-tan) 0%, #a8743d 50%, var(--photo-dark) 100%);
    border-radius: 46% 50% 6px 6px / 36% 40% 6px 6px;
  }

  .brand-name {
    position: absolute; left: 200px; top: 44px;
    font-family: "Archivo", sans-serif; font-weight: 800;
    font-size: 46px; color: var(--ink); letter-spacing: -0.5px;
  }
  .tagline {
    position: absolute; left: 110px; top: 112px; width: 430px;
    font-family: "Carlito", sans-serif; font-weight: 700;
    font-size: 15px; line-height: 1.15; color: var(--ink); text-align: right;
  }
  .person-name {
    position: absolute; left: 190px; top: 180px;
    font-family: "PT Sans Narrow", sans-serif;
    font-size: 30px; color: var(--ink);
  }
  .byline {
    position: absolute; left: 190px; top: 240px;
    font-family: "Dancing Script", cursive; font-weight: 600;
    font-size: 30px; color: var(--brand-red);
  }

  .contact-item { position: absolute; text-align: center; }
  .contact-icon {
    display: block; margin: 0 auto 10px;
    width: 58px; height: 58px;
  }
  .contact-text {
    font-family: "Carlito", sans-serif; font-size: 21px;
    color: var(--contact-text); letter-spacing: 0.5px; white-space: nowrap;
  }
  .contact-email { left: 20px; top: 356px; width: 300px; }
  .contact-web { left: 330px; top: 416px; width: 300px; }
  .contact-phone { left: 690px; top: 452px; width: 240px; }
  .contact-phone .contact-text { font-size: 24px; letter-spacing: 1.5px; }
</style>
</head>
<body>
  <div class="business-card">
    <div class="contact-band"></div>
    <div class="panel-divider"></div>

    <div class="photo-panel">
      <div class="dog-photo" role="img" aria-label="Photograph of a German Shepherd dog standing, facing right"></div>
    </div>

    <div class="brand-name">Jolly Hounds</div>
    <div class="tagline">Qualified Dog Behavioural<br>Trainer and Natural Animal Healthcare Consultant</div>
    <div class="person-name">Rebecca Thornbury</div>
    <div class="byline">Happy Dogs, Happy Owners</div>

    <div class="contact-item contact-email">
      <svg class="contact-icon" viewBox="0 0 58 58" aria-hidden="true">
        <circle cx="29" cy="29" r="27" fill="var(--icon-fill)" stroke="var(--icon-ring)" stroke-width="2"/>
        <rect x="15" y="19" width="28" height="20" fill="none" stroke="var(--icon-ink)" stroke-width="2.5"/>
        <polyline points="15,19 29,31 43,19" fill="none" stroke="var(--icon-ink)" stroke-width="2.5"/>
      </svg>
      <span class="contact-text">jollyhounds7@fernpost.example</span>
    </div>

    <div class="contact-item contact-web">
      <svg class="contact-icon" viewBox="0 0 58 58" aria-hidden="true">
        <circle cx="29" cy="29" r="27" fill="var(--icon-fill)" stroke="var(--icon-ring)" stroke-width="2"/>
        <polyline points="13,30 29,15 45,30" fill="none" stroke="var(--icon-ink)" stroke-width="2.5"/>
        <polyline points="18,26 18,43 40,43 40,26" fill="none" stroke="var(--icon-ink)" stroke-width="2.5"/>
        <rect x="25" y="32" width="8" height="11" fill="none" stroke="var(--icon-ink)" stroke-width="2"/>
      </svg>
      <span class="contact-text">www.jollyhounds7.example</span>
    </div>

    <div class="contact-item contact-phone">
      <svg class="contact-icon" viewBox="0 0 58 58" aria-hidden="true">
        <circle cx="29" cy="29" r="27" fill="var(--icon-fill)" stroke="var(--icon-ring)" stroke-width="2"/>
        <path d="M14 24 Q29 12 44 24 L40 28 L36 24 L22 24 L18 28 Z" fill="var(--icon-ink)"/>
        <rect x="17" y="28" width="24" height="15" rx="2" fill="none" stroke="var(--icon-ink)" stroke-width="2.5"/>
        <g fill="var(--icon-ink)">
          <rect x="22" y="32" width="3" height="3"/><rect x="27.5" y="32" width="3" height="3"/><rect x="33" y="32" width="3" height="3"/>
          <rect x="22" y="37" width="3" height="3"/><rect x="27.5" y="37" width="3" height="3"/><rect x="33" y="37" width="3" height="3"/>
        </g>
      </svg>
      <span class="contact-text">0427 861350</span>
    </div>
  </div>
</body>
</html>
```